High value cover design for an A4 ideation pad.

The product is NOT A BOOK.

It's an A4 ideation pad for professionals, designers and creators who handwrite their ideas. Visualise creators like Milo Varnet, Owen Plaskit and Gregor Lunwick in your mind's eye.

I'm looking for a cover design for the ideation pad. Both front and back.

It should look, feel and convey the following.

--> A handcrafted product experience

--> High value & Elegance

--> Inspiration

Mandatory --> See Uploaded Files --> Files 1, 5 & 6

Target Market(s)

- Designers

-Creative Professionals

- Entrepreneurs

who handwrite their ideas. Visualise creators like Milo Varnet, Owen Plaskit and Gregor Lunwick in your mind's eye.

Industry/Entity Type

Stationary

Font styles to use
Script
Other font styles liked:
• Calligraphy

Colors
fbed22

Requirements
Must have
• Title text - Quiet Kettle Notes

-Text in gold on brown leather background to convey high value for the front cover.

--> High value & Elegance

--> Inspiration

--> Should compel the customers to pick up and own the idea pad
Nice to have
• That's my take but other ideas are welcome
Should not have
• Must not convey

- low value

```html
<!DOCTYPE html>
<html lang="en">
<head>
<meta charset="utf-8">
<title>Quiet Kettle Notes – Ideation Pad Covers</title>
<link rel="stylesheet" href="https://fonts.googleapis.com/css2?family=Pinyon+Script&display=swap">
<style>
  :root {
    --canvas-bg: #ffffff;
    --leather-base: #d9742f;
    --leather-light: #e48a45;
    --leather-dark: #c9652a;
    --gold-light: #fbe9a8;
    --gold-mid: #e6bf72;
    --gold-deep: #b8863a;
    --coil: #4a4a4a;
    --coil-shine: #8a8a8a;
    --cover-shadow: rgba(60, 30, 10, 0.3);
  }
  * { margin: 0; padding: 0; box-sizing: border-box; }
  html, body {
    width: 1200px;
    height: 1026px;
    overflow: hidden;
    background: var(--canvas-bg);
  }
  .spread {
    position: relative;
    width: 1200px;
    height: 1026px;
  }
  .cover {
    position: absolute;
    width: 558px;
    height: 778px;
    background:
      radial-gradient(ellipse at 30% 20%, var(--leather-light) 0%, transparent 55%),
      radial-gradient(ellipse at 75% 70%, var(--leather-light) 0%, transparent 50%),
      radial-gradient(ellipse at 60% 40%, var(--leather-dark) 0%, transparent 60%),
      var(--leather-base);
    box-shadow: 0 2px 6px var(--cover-shadow);
  }
  .cover--back { left: 573px; top: 194px; }
  .cover--front { left: 117px; top: 116px; }

  .binding {
    position: absolute;
    overflow: visible;
  }
  .binding--back { left: 674px; top: 176px; width: 430px; height: 52px; }
  .binding--front { left: 144px; top: 98px; width: 520px; height: 52px; }

  .figure-art {
    position: absolute;
    left: 47px;
    top: 121px;
    width: 390px;
    height: 507px;
  }

  .title { position: absolute; inset: 0; pointer-events: none; }
  .title__word {
    position: absolute;
    display: block;
    white-space: nowrap;
    font-family: "Pinyon Script", cursive;
    font-weight: 400;
    line-height: 1;
    color: var(--gold-mid);
    background: linear-gradient(170deg, var(--gold-light) 0%, var(--gold-mid) 50%, var(--gold-deep) 100%);
    -webkit-background-clip: text;
    background-clip: text;
    -webkit-text-fill-color: transparent;
  }
  .title__word--lead, .title__word--tail { font-size: 54px; }
  .title__word--mid { font-size: 24px; }

  .cover--front .title__word--lead { left: 362px; top: 358px; }
  .cover--front .title__word--mid  { left: 382px; top: 428px; }
  .cover--front .title__word--tail { left: 316px; top: 448px; }

  .cover--back .title__word--lead { left: 214px; top: 310px; }
  .cover--back .title__word--mid  { left: 208px; top: 384px; }
  .cover--back .title__word--tail { left: 254px; top: 392px; }
</style>
</head>
<body>
  <main class="spread">
    <svg width="0" height="0" style="position:absolute" aria-hidden="true">
      <defs>
        <symbol id="coil" viewBox="0 0 24 52">
          <rect x="2" y="2" width="12" height="48" rx="6" fill="none" stroke="var(--coil)" stroke-width="3.5"/>
          <rect x="9" y="2" width="12" height="48" rx="6" fill="none" stroke="var(--coil)" stroke-width="3.5"/>
          <line x1="5" y1="10" x2="5" y2="40" stroke="var(--coil-shine)" stroke-width="1"/>
        </symbol>
      </defs>
    </svg>

    <section class="cover cover--back" aria-label="Back cover">
      <p class="title">
        <span class="title__word title__word--lead">Quiet</span>
        <span class="title__word title__word--mid">Kettle</span>
        <span class="title__word title__word--tail">Notes</span>
      </p>
    </section>
    <svg class="binding binding--back" viewBox="0 0 430 52" aria-hidden="true">
      <use href="#coil" x="0" width="24" height="52"/>
      <use href="#coil" x="37" width="24" height="52"/>
      <use href="#coil" x="74" width="24" height="52"/>
      <use href="#coil" x="111" width="24" height="52"/>
      <use href="#coil" x="148" width="24" height="52"/>
      <use href="#coil" x="185" width="24" height="52"/>
      <use href="#coil" x="222" width="24" height="52"/>
      <use href="#coil" x="259" width="24" height="52"/>
      <use href="#coil" x="296" width="24" height="52"/>
      <use href="#coil" x="333" width="24" height="52"/>
      <use href="#coil" x="370" width="24" height="52"/>
      <use href="#coil" x="406" width="24" height="52"/>
    </svg>

    <section class="cover cover--front" aria-label="Front cover">
      <svg class="figure-art" viewBox="0 0 390 507" role="img" aria-label="Gold line illustration of a leaping figure with outstretched arms">
        <defs>
          <radialGradient id="figureGlow" cx="55%" cy="45%" r="55%">
            <stop offset="0%" stop-color="#e9b264" stop-opacity="0.5"/>
            <stop offset="100%" stop-color="#d9742f" stop-opacity="0"/>
          </radialGradient>
        </defs>
        <rect width="390" height="507" fill="url(#figureGlow)"/>
      </svg>
      <h1 class="title">
        <span class="title__word title__word--lead">Quiet</span>
        <span class="title__word title__word--mid">Kettle</span>
        <span class="title__word title__word--tail">Notes</span>
      </h1>
    </section>
    <svg class="binding binding--front" viewBox="0 0 520 52" aria-hidden="true">
      <use href="#coil" x="0" width="24" height="52"/>
      <use href="#coil" x="38" width="24" height="52"/>
      <use href="#coil" x="76" width="24" height="52"/>
      <use href="#coil" x="114" width="24" height="52"/>
      <use href="#coil" x="152" width="24" height="52"/>
      <use href="#coil" x="190" width="24" height="52"/>
      <use href="#coil" x="228" width="24" height="52"/>
      <use href="#coil" x="266" width="24" height="52"/>
      <use href="#coil" x="304" width="24" height="52"/>
      <use href="#coil" x="342" width="24" height="52"/>
      <use href="#coil" x="380" width="24" height="52"/>
      <use href="#coil" x="418" width="24" height="52"/>
      <use href="#coil" x="456" width="24" height="52"/>
      <use href="#coil" x="494" width="24" height="52"/>
    </svg>
  </main>
</body>
</html>
```